New Business Card Design Project

I need a design for business cards, i am an electrical business called "Corvane Electrical and Communications" i need the cards to be double sided with the company logo on the back (attached) the front needs to say my company name, web site, email address, telephone number, and ABN number and electrical license number. I am open to different arrangements of the information but would like the background to be incorporating something electrical or something that looks smart. open to all additional ideas also.

The company colours are orange and grey see logo attached.

Business Name: Corvane Electrical and Communications
Website: corvaneelectricalandcomms.example.com.au
Email: brent@corvaneelectricalandcomms.example.com.au
Telephone(mobile): 0481209736
ABN: 71208349162
Lic No: 418273D

Target Market(s)

Business entities, Project Managers, Accounts, Clients

Industry/Entity Type

Electrician

Contact Information for Business Card

I need a design for business cards, i am an electrical business called "Corvane Electrical and Communications" i need the cards to be double sided with the company logo on the back (attached) the front needs to say my company name

Font styles to use
Serif
Sans Serif

Colors
f37122
5c5c5c

Requirements
Must have
• Must have the Logo on the back open to different ways of it being on the back but had in mind to keep it central but again open to other options
Nice to have
• A real modern cool background that is eye catching yet contemporary
Should not have
• No backgrounds of a light bulb or plug or anything like that

```html
<!DOCTYPE html>
<html lang="en">
<head>
<meta charset="utf-8">
<title>Corvane Electrical and Communications – Business Card</title>
<link rel="stylesheet" href="https://fonts.googleapis.com/css2?family=Arimo:wght@400;700&display=swap">
<style>
  :root {
    --canvas: #d9d9d9;
    --card-grey: #5c5c5c;
    --card-grey-dark: #4a4a4a;
    --card-grey-light: #6a6a6a;
    --accent: #f5a81c;
    --accent-deep: #e9971a;
    --ink: #5c5c5c;
    --white: #f4f4f4;
    --muted: #b9b9b9;
  }
  * { box-sizing: border-box; margin: 0; padding: 0; }
  html, body {
    width: 1200px;
    height: 950px;
    overflow: hidden;
    background: var(--canvas);
    font-family: "Arimo", Arial, sans-serif;
  }
  .card {
    position: absolute;
    left: 232px;
    width: 735px;
    height: 420px;
    overflow: hidden;
    box-shadow: 0 6px 18px rgba(0,0,0,0.25);
  }
  .card--back {
    top: 35px;
    background: linear-gradient(135deg, var(--card-grey-light), var(--card-grey) 55%, var(--card-grey-dark));
  }
  .card--front {
    top: 495px;
    background: var(--card-grey);
  }
  .card__waves { position: absolute; inset: 0; width: 100%; height: 100%; }

  .brand {
    display: flex;
    align-items: center;
    gap: 14px;
    color: var(--white);
    font-weight: 700;
  }
  .brand__dot {
    width: 26px; height: 26px;
    border-radius: 50%;
    background: var(--accent);
    flex: none;
  }
  .brand__name { font-size: 60px; letter-spacing: 2px; line-height: 1; text-transform: uppercase; }
  .brand__line { font-size: 14px; letter-spacing: 1.2px; text-transform: uppercase; margin-top: 6px; }

  .card--back .brand {
    position: absolute;
    left: 50%;
    top: 150px;
    transform: translateX(-50%);
  }
  .back__web {
    position: absolute;
    left: 0; right: 0;
    top: 268px;
    text-align: center;
    color: var(--muted);
    font-size: 17px;
    letter-spacing: 0.5px;
  }

  .card--front .brand { position: absolute; left: 36px; top: 60px; }
  .card--front .brand__name { font-size: 50px; }
  .card--front .brand__line { font-size: 12px; }

  .contact {
    position: absolute;
    right: 34px;
    top: 232px;
    text-align: right;
    color: var(--ink);
    font-size: 17px;
    line-height: 21px;
  }
  .contact__name { font-weight: 700; font-size: 20px; letter-spacing: 1px; }
  .contact__title { font-size: 15px; letter-spacing: 1px; margin-bottom: 2px; }
  .contact__row { display: flex; justify-content: flex-end; align-items: center; gap: 8px; }
  .contact__row svg { width: 15px; height: 15px; flex: none; }
</style>
</head>
<body>

<section class="card card--back" aria-label="Business card back">
  <div class="brand">
    <span class="brand__dot"></span>
    <div>
      <div class="brand__name">Corvane</div>
      <div class="brand__line">Electrical &amp; Communications</div>
    </div>
  </div>
  <p class="back__web">corvaneelectricalandcomms.example.com.au</p>
</section>

<section class="card card--front" aria-label="Business card front">
  <svg class="card__waves" viewBox="0 0 735 420" preserveAspectRatio="none" aria-hidden="true">
    <path d="M0,245 C140,205 250,250 370,255 C500,258 590,175 735,185 L735,420 L0,420 Z" fill="var(--accent)"/>
    <path d="M25,262 C120,238 230,248 300,262 C220,256 120,256 25,262 Z" fill="var(--card-grey)"/>
    <path d="M420,232 C520,200 610,178 700,205 C610,192 520,208 420,232 Z" fill="var(--card-grey)"/>
  </svg>

  <div class="brand">
    <span class="brand__dot"></span>
    <div>
      <div class="brand__name">Corvane</div>
      <div class="brand__line">Electrical &amp; Communications</div>
    </div>
  </div>

  <div class="contact">
    <div class="contact__name">DANA HOLT</div>
    <div class="contact__title">PRESIDENT</div>
    <div class="contact__row">ABN: 71208349162</div>
    <div class="contact__row">Lic No: 418273D</div>
    <div class="contact__row">0481209736
      <svg viewBox="0 0 16 16" aria-hidden="true"><rect x="4" y="1" width="8" height="14" rx="1.5" fill="var(--ink)"/><rect x="5.5" y="3" width="5" height="8" fill="var(--accent)"/></svg>
    </div>
    <div class="contact__row">brent@corvaneelectricalandcomms.example.com.au
      <svg viewBox="0 0 16 16" aria-hidden="true"><rect x="1" y="3" width="14" height="10" rx="1" fill="var(--ink)"/><path d="M1.5,3.5 L8,9 L14.5,3.5" fill="none" stroke="var(--accent)" stroke-width="1.3"/></svg>
    </div>
    <div class="contact__row">corvaneelectricalandcomms.example.com.au
      <svg viewBox="0 0 16 16" aria-hidden="true"><circle cx="8" cy="8" r="7" fill="var(--ink)"/><ellipse cx="8" cy="8" rx="3" ry="7" fill="none" stroke="var(--accent)" stroke-width="1"/><path d="M1,8 H15" stroke="var(--accent)" stroke-width="1"/></svg>
    </div>
  </div>
</section>

</body>
</html>
```